New business card/stationary for a consulting company

I am looking for a clean and very professional looking business card for my consulting company as well as corresponding stationary. I am uploading our logo. I like simple and powerful for the feel. No graphics but I am open on everything else. Below is my contact information but would like the final to be in a version I can add my employees information into and print. Thank you.

Daniel Whitcombe
dan@ferncliffadvisory.com
2870 North 9th Avenue, Summit Floor, Elm Ridge, Illinois 60531
www.ferncliffadvisory.com

Industry/Entity Type

Consulting

Contact Information for Business Card

Daniel Whitcombe
dan@ferncliffadvisory.com
www.ferncliffadvisory.com

Font styles to use
Serif
Sans Serif

Requirements
Must have
• Our logo and the business card details.
Nice to have
• our website www.ferncliffadvisory.com

```html
<!DOCTYPE html>
<html lang="en">
<head>
<meta charset="utf-8">
<title>Ferncliff Advisory – Business Card</title>
<link rel="stylesheet" href="https://fonts.googleapis.com/css2?family=Source+Sans+3:wght@300;400;600;700&display=swap">
<style>
  :root {
    --navy: #0b0a6b;
    --navy-deep: #07064f;
    --paper: #f5f5f5;
    --ink: #555555;
    --stage: #e6e6e9;
  }
  * { box-sizing: border-box; margin: 0; padding: 0; }
  html, body {
    width: 1200px; height: 900px; overflow: hidden;
    background: var(--stage);
    font-family: "Source Sans 3", sans-serif;
  }
  .canvas {
    width: 1200px; height: 900px;
    display: flex; flex-direction: column; align-items: center; justify-content: center;
    gap: 56px;
  }
  .card {
    position: relative;
    width: 620px; height: 354px;
    box-shadow: 0 10px 28px rgba(0,0,0,.22);
    overflow: hidden;
  }
  /* Front */
  .card-front {
    background: var(--navy);
    color: #fff;
    display: flex; flex-direction: column; align-items: center; justify-content: center;
  }
  .brand { display: flex; align-items: center; gap: 14px; }
  .brand-square { width: 26px; height: 26px; }
  .brand-name {
    font-weight: 400; letter-spacing: .06em; text-transform: uppercase;
  }
  .card-front .brand-square { background: #fff; }
  .card-front .brand-name { font-size: 30px; color: #fff; }
  .front-web {
    margin-top: 38px;
    font-size: 15px; letter-spacing: .42em; font-weight: 300;
  }
  /* Back */
  .card-back { background: var(--paper); }
  .back-band { position: absolute; top: 0; left: 0; width: 620px; height: 90px; }
  .holder-name {
    position: absolute; top: 18px; right: 34px;
    color: #fff; font-weight: 700; font-size: 17px; letter-spacing: .02em;
    text-transform: uppercase;
  }
  .back-body { position: absolute; left: 58px; top: 150px; }
  .card-back .brand-square { background: var(--navy); }
  .card-back .brand-name { font-size: 27px; color: var(--navy); }
  .address, .contact-line {
    font-size: 15px; color: var(--ink); line-height: 1.45;
  }
  .address { margin-top: 26px; }
  .contact-line .label { color: var(--navy); font-weight: 700; }
  .contact-line .item + .label { margin-left: 10px; }
</style>
</head>
<body>
<main class="canvas">
  <section class="card card-front">
    <div class="brand">
      <span class="brand-square"></span>
      <span class="brand-name">Ferncliff Advisory</span>
    </div>
    <p class="front-web">www.ferncliffadvisory.com</p>
  </section>

  <section class="card card-back">
    <svg class="back-band" viewBox="0 0 620 90" aria-hidden="true">
      <polygon points="0,0 620,0 620,56 330,56 300,74 270,40 0,40" fill="var(--navy)"/>
      <polyline points="0,52 262,52 300,86 338,66 620,66" fill="none" stroke="var(--navy)" stroke-width="4"/>
    </svg>
    <p class="holder-name">Daniel Whitcombe</p>
    <div class="back-body">
      <div class="brand">
        <span class="brand-square"></span>
        <span class="brand-name">Ferncliff Advisory</span>
      </div>
      <p class="address">2870 North 9th Avenue, Summit Floor, Elm Ridge, Illinois 60531</p>
      <p class="contact-line">
        <span class="label">E:</span> <span class="item">dan@ferncliffadvisory.com</span>
        <span class="label">W:</span> <span class="item">ferncliffadvisory.com</span>
      </p>
    </div>
  </section>
</main>
</body>
</html>
```